World travel poster - I want to remember where I've been!

I would like a poster for me to print and keep in my home as a record of my world travels. It must look like a mechanical sign in an airport (see picture for example) However I am flexible with exact layout, if you'd like to add images used to enhance poster etc. I have also uploaded some pictures from my travels if you would like to use some or all of them. They are named according to location.

Poster must include:
USA 2003
Malaysia 2006
Thailand 2007
Italy 2009
India, Vietnam, Hong Kong 2010
Bali 2011
Malaysia 2012
Singapore 2012
Vietnam, Cambodia, Laos 2013
Europe 2015

and the quote:

"The world is a book and those who do not travel read only one page."
― Severin of Caldra
Updates

Hi there. I have uploaded some photos of my travels to possibly use in my poster. They are named according to location. I haven't decided if I prefer the originial layout or with images, so please post both for me to consider. Thanks so much for your time to consider my project.

Target Market(s)

Something to catch the eye of visitors and remind me of my adventures.
A classic piece that is a conversation starter.

Industry/Entity Type

Airport

Font styles to use
Other font styles liked:
• Airport mechanical font

Requirements
Must have
• Some lettering like a mechanical airport board (see image attached for example).
Dimensions that are easy to print - either A3, or a long/narrow poster.
Nice to have
• A splash of colour or an image, maybe the words 'arrivals' or 'departures'

Use of some of my pictures if it doesn't look too busy.
Should not have
• Anything too over the top.

```html
<!DOCTYPE html>
<html lang="en">
<head>
<meta charset="utf-8">
<title>Departures – Travel Record</title>
<link href="https://fonts.googleapis.com/css2?family=Arimo:wght@700&family=Barlow+Condensed:wght@500&display=swap" rel="stylesheet">
<style>
  :root{
    --board:#2f3b3d;
    --band:#364446;
    --panel:#2b3537;
    --panel-edge:#121819;
    --flap-top:#2f393b;
    --flap-bottom:#273032;
    --flap-edge:#151b1c;
    --seam:#1a2122;
    --amber:#f6dd12;
    --white:#ffffff;
    --red:#ee2222;
  }
  html,body{margin:0;padding:0;overflow:hidden;background:var(--board);}
  .board{position:relative;width:1200px;height:967px;background:var(--board);overflow:hidden;font-family:"Arimo",Arial,sans-serif;color:var(--white);}
  .panel{position:absolute;left:16px;width:1172px;background:var(--panel);border:2px solid var(--panel-edge);border-radius:4px;box-sizing:border-box;}
  .panel::after{content:"";position:absolute;left:0;right:0;top:50%;height:1px;background:var(--seam);}
  .header{top:20px;height:123px;}
  .plane-badge{position:absolute;left:85px;top:12px;width:95px;height:97px;}
  .title{position:absolute;left:258px;top:4px;margin:0;font-size:101px;letter-spacing:-3.5px;line-height:116px;font-weight:700;z-index:1;}
  .col-label{position:absolute;top:150px;margin:0;font-size:40px;font-weight:700;line-height:48px;}
  .col-label.dest{left:149px;}
  .col-label.time{right:57px;}
  .rows{position:absolute;left:0;top:200px;width:1200px;}
  .row{box-sizing:border-box;height:56px;margin-bottom:6.5px;background:var(--band);display:grid;grid-template-columns:repeat(28,38px);column-gap:3.63px;padding:2px 0 0 20px;}
  .flap{position:relative;height:52px;box-sizing:border-box;background:linear-gradient(var(--flap-top),var(--flap-bottom));border:1px solid var(--flap-edge);border-radius:2px;font-family:"Barlow Condensed",sans-serif;font-weight:500;font-size:50px;line-height:52px;text-align:center;color:var(--amber);font-style:normal;}
  .flap::after{content:"";position:absolute;left:0;right:0;top:50%;height:1px;background:var(--seam);}
  .footer{top:826px;height:122px;}
  .quote{position:absolute;left:0;right:0;top:19px;margin:0;text-align:center;font-size:33px;line-height:40px;font-weight:700;z-index:1;}
  .author{position:absolute;right:25px;top:62px;margin:0;font-size:33px;line-height:40px;font-weight:700;z-index:1;}
</style>
</head>
<body>
<main class="board">
  <header class="panel header">
    <svg class="plane-badge" viewBox="0 0 95 97" aria-hidden="true">
      <rect width="95" height="97" rx="9" fill="var(--red)"/>
      <path d="M47.5 8c3 0 4 5 4 11v18l32 18v6l-32-9v19l9 6v5l-13-3-13 3v-5l9-6V52l-32 9v-6l32-18V19c0-6 1-11 4-11z" fill="var(--white)"/>
    </svg>
    <h1 class="title">DEPARTURES</h1>
  </header>

  <p class="col-label dest">Destination</p>
  <p class="col-label time">Time</p>

  <section class="rows">
    <div class="row"><i class="flap">U</i><i class="flap">S</i><i class="flap">A</i><i class="flap"></i><i class="flap"></i><i class="flap"></i><i class="flap"></i><i class="flap"></i><i class="flap"></i><i class="flap"></i><i class="flap"></i><i class="flap"></i><i class="flap"></i><i class="flap"></i><i class="flap"></i><i class="flap"></i><i class="flap"></i><i class="flap"></i><i class="flap"></i><i class="flap"></i><i class="flap"></i><i class="flap"></i><i class="flap"></i><i class="flap"></i><i class="flap">2</i><i class="flap">0</i><i class="flap">0</i><i class="flap">3</i></div>
    <div class="row"><i class="flap">M</i><i class="flap">A</i><i class="flap">L</i><i class="flap">A</i><i class="flap">Y</i><i class="flap">S</i><i class="flap">I</i><i class="flap">A</i><i class="flap"></i><i class="flap"></i><i class="flap"></i><i class="flap"></i><i class="flap"></i><i class="flap"></i><i class="flap"></i><i class="flap"></i><i class="flap"></i><i class="flap"></i><i class="flap"></i><i class="flap"></i><i class="flap"></i><i class="flap"></i><i class="flap"></i><i class="flap"></i><i class="flap">2</i><i class="flap">0</i><i class="flap">0</i><i class="flap">6</i></div>
    <div class="row"><i class="flap">T</i><i class="flap">H</i><i class="flap">A</i><i class="flap">I</i><i class="flap">L</i><i class="flap">A</i><i class="flap">N</i><i class="flap">D</i><i class="flap"></i><i class="flap"></i><i class="flap"></i><i class="flap"></i><i class="flap"></i><i class="flap"></i><i class="flap"></i><i class="flap"></i><i class="flap"></i><i class="flap"></i><i class="flap"></i><i class="flap"></i><i class="flap"></i><i class="flap"></i><i class="flap"></i><i class="flap"></i><i class="flap">2</i><i class="flap">0</i><i class="flap">0</i><i class="flap">7</i></div>
    <div class="row"><i class="flap">I</i><i class="flap">T</i><i class="flap">A</i><i class="flap">L</i><i class="flap">Y</i><i class="flap"></i><i class="flap"></i><i class="flap"></i><i class="flap"></i><i class="flap"></i><i class="flap"></i><i class="flap"></i><i class="flap"></i><i class="flap"></i><i class="flap"></i><i class="flap"></i><i class="flap"></i><i class="flap"></i><i class="flap"></i><i class="flap"></i><i class="flap"></i><i class="flap"></i><i class="flap"></i><i class="flap"></i><i class="flap">2</i><i class="flap">0</i><i class="flap">0</i><i class="flap">9</i></div>
    <div class="row"><i class="flap">I</i><i class="flap">N</i><i class="flap">D</i><i class="flap">I</i><i class="flap">A</i><i class="flap"></i><i class="flap">V</i><i class="flap">I</i><i class="flap">E</i><i class="flap">T</i><i class="flap">N</i><i class="flap">A</i><i class="flap">M</i><i class="flap"></i><i class="flap">H</i><i class="flap">O</i><i class="flap">N</i><i class="flap">G</i><i class="flap"></i><i class="flap">K</i><i class="flap">O</i><i class="flap">N</i><i class="flap">G</i><i class="flap"></i><i class="flap">2</i><i class="flap">0</i><i class="flap">1</i><i class="flap">0</i></div>
    <div class="row"><i class="flap">B</i><i class="flap">A</i><i class="flap">L</i><i class="flap">I</i><i class="flap"></i><i class="flap"></i><i class="flap"></i><i class="flap"></i><i class="flap"></i><i class="flap"></i><i class="flap"></i><i class="flap"></i><i class="flap"></i><i class="flap"></i><i class="flap"></i><i class="flap"></i><i class="flap"></i><i class="flap"></i><i class="flap"></i><i class="flap"></i><i class="flap"></i><i class="flap"></i><i class="flap"></i><i class="flap"></i><i class="flap">2</i><i class="flap">0</i><i class="flap">1</i><i class="flap">1</i></div>
    <div class="row"><i class="flap">M</i><i class="flap">A</i><i class="flap">L</i><i class="flap">A</i><i class="flap">Y</i><i class="flap">S</i><i class="flap">I</i><i class="flap">A</i><i class="flap"></i><i class="flap"></i><i class="flap"></i><i class="flap"></i><i class="flap"></i><i class="flap"></i><i class="flap"></i><i class="flap"></i><i class="flap"></i><i class="flap"></i><i class="flap"></i><i class="flap"></i><i class="flap"></i><i class="flap"></i><i class="flap"></i><i class="flap"></i><i class="flap">2</i><i class="flap">0</i><i class="flap">1</i><i class="flap">2</i></div>
    <div class="row"><i class="flap">S</i><i class="flap">I</i><i class="flap">N</i><i class="flap">G</i><i class="flap">A</i><i class="flap">P</i><i class="flap">O</i><i class="flap">R</i><i class="flap">E</i><i class="flap"></i><i class="flap"></i><i class="flap"></i><i class="flap"></i><i class="flap"></i><i class="flap"></i><i class="flap"></i><i class="flap"></i><i class="flap"></i><i class="flap"></i><i class="flap"></i><i class="flap"></i><i class="flap"></i><i class="flap"></i><i class="flap"></i><i class="flap">2</i><i class="flap">0</i><i class="flap">1</i><i class="flap">2</i></div>
    <div class="row"><i class="flap">V</i><i class="flap">I</i><i class="flap">E</i><i class="flap">T</i><i class="flap">N</i><i class="flap">A</i><i class="flap">M</i><i class="flap"></i><i class="flap">C</i><i class="flap">A</i><i class="flap">M</i><i class="flap">B</i><i class="flap">O</i><i class="flap">D</i><i class="flap">I</i><i class="flap">A</i><i class="flap"></i><i class="flap">L</i><i class="flap">A</i><i class="flap">O</i><i class="flap">S</i><i class="flap"></i><i class="flap"></i><i class="flap"></i><i class="flap">2</i><i class="flap">0</i><i class="flap">1</i><i class="flap">3</i></div>
    <div class="row"><i class="flap">E</i><i class="flap">U</i><i class="flap">R</i><i class="flap">O</i><i class="flap">P</i><i class="flap">E</i><i class="flap"></i><i class="flap"></i><i class="flap"></i><i class="flap"></i><i class="flap"></i><i class="flap"></i><i class="flap"></i><i class="flap"></i><i class="flap"></i><i class="flap"></i><i class="flap"></i><i class="flap"></i><i class="flap"></i><i class="flap"></i><i class="flap"></i><i class="flap"></i><i class="flap"></i><i class="flap"></i><i class="flap">2</i><i class="flap">0</i><i class="flap">1</i><i class="flap">5</i></div>
  </section>

  <footer class="panel footer">
    <p class="quote">"The world is a book and those who do not travel read only one page."</p>
    <p class="author">— Severin of Caldra</p>
  </footer>
</main>
</body>
</html>
```